Tolbek cards

I want a simple business card that pops.
Logo on one side.
On side two i want.
"Are you thinking about a new building on your property, or renovating an existing structure? Contact".....
Owners Name: Dale Whitacre
Owners Phone number: 610-555-0187
Address:4076 Copper Ridge RD, Brenwick, OH 43918
Committed to Quality, Service, and Integrity

```html
<!DOCTYPE html>
<html lang="en">
<head>
<meta charset="utf-8">
<title>Tolbek Builders LLC – Business Cards</title>
<link rel="stylesheet" href="https://fonts.googleapis.com/css2?family=Poppins:wght@400;500;600;700&display=swap">
<style>
  :root {
    --page-bg: #f0f0f0;
    --card-bg: #ffffff;
    --brown-dark: #432f1c;
    --brown-deep: #58381f;
    --brown-light: #a48f77;
    --ink: #1d1d1d;
  }
  * { box-sizing: border-box; margin: 0; padding: 0; }
  html, body { width: 1200px; height: 990px; overflow: hidden; }
  body {
    background: var(--page-bg);
    font-family: "Poppins", sans-serif;
    position: relative;
  }
  .card {
    position: absolute;
    left: 244px;
    width: 712px;
    height: 407px;
    background: var(--card-bg);
    border-radius: 34px;
    overflow: hidden;
  }
  .card--front { top: 68px; }
  .card--back { top: 515px; }

  .card__band {
    position: absolute;
    left: 0; bottom: 0;
    width: 100%;
    height: 26px;
  }

  .brand {
    position: absolute;
    display: flex;
    flex-direction: column;
    align-items: center;
    color: var(--brown-dark);
    font-weight: 700;
    text-transform: uppercase;
    line-height: 1;
  }
  .brand__mark {
    width: 56px; height: 56px;
    background: var(--brown-dark);
  }
  .brand__name { letter-spacing: 1px; }
  .brand__suffix { letter-spacing: 2px; }

  .card--front .brand { left: 0; right: 0; top: 78px; }
  .card--front .brand__mark { width: 78px; height: 78px; margin-bottom: 22px; }
  .card--front .brand__name { font-size: 82px; }
  .card--front .brand__suffix { font-size: 25px; margin-top: 8px; }

  .card--back .brand { left: 50px; width: 270px; top: 118px; }
  .card--back .brand__mark { margin-bottom: 16px; }
  .card--back .brand__name { font-size: 54px; }
  .card--back .brand__suffix { font-size: 17px; margin-top: 6px; }

  .divider {
    position: absolute;
    left: 357px; top: 93px;
    width: 1px; height: 221px;
    background: var(--brown-deep);
  }

  .contact {
    position: absolute;
    left: 402px; top: 100px;
    color: var(--ink);
  }
  .contact__name {
    font-size: 35px; font-weight: 600;
    color: var(--brown-dark);
    line-height: 1.05;
  }
  .contact__role { font-size: 16px; font-weight: 500; line-height: 1.1; }
  .contact__tagline { font-size: 17px; line-height: 23px; margin-top: 14px; }
  .contact__list { list-style: none; margin-top: 16px; font-size: 17px; line-height: 23px; }
  .contact__item { display: flex; align-items: flex-start; gap: 10px; }
  .contact__icon { width: 15px; height: 18px; flex: none; margin-top: 2px; fill: var(--brown-dark); }

  .pitch {
    position: absolute;
    left: 0; right: 0; top: 326px;
    text-align: center;
    font-size: 18px;
    line-height: 24px;
    color: var(--ink);
  }
</style>
</head>
<body>

<section class="card card--front" aria-label="Card front">
  <div class="brand">
    <div class="brand__mark"></div>
    <div class="brand__name">Tolbek</div>
    <div class="brand__suffix">Builders LLC</div>
  </div>
  <svg class="card__band" viewBox="0 0 712 26" preserveAspectRatio="none" aria-hidden="true">
    <defs>
      <linearGradient id="band-front" x1="0" x2="1" y1="0" y2="0">
        <stop offset="0" stop-color="#a48f77"/>
        <stop offset="0.46" stop-color="#58381f"/>
        <stop offset="0.6" stop-color="#58381f"/>
        <stop offset="1" stop-color="#a48f77"/>
      </linearGradient>
    </defs>
    <rect width="712" height="26" fill="url(#band-front)"/>
    <polygon points="317,0 344,0 381,26 354,26" fill="#ffffff"/>
  </svg>
</section>

<section class="card card--back" aria-label="Card back">
  <div class="brand">
    <div class="brand__mark"></div>
    <div class="brand__name">Tolbek</div>
    <div class="brand__suffix">Builders LLC</div>
  </div>

  <div class="divider"></div>

  <div class="contact">
    <h1 class="contact__name">Dale Whitacre</h1>
    <p class="contact__role">Owners</p>
    <p class="contact__tagline">Committed to Quality,<br>Service, and Integrity</p>
    <ul class="contact__list">
      <li class="contact__item">
        <svg class="contact__icon" viewBox="0 0 24 24" aria-hidden="true"><path d="M6.6 10.8a15.1 15.1 0 0 0 6.6 6.6l2.2-2.2a1 1 0 0 1 1-.25 11.4 11.4 0 0 0 3.6.57 1 1 0 0 1 1 1V20a1 1 0 0 1-1 1A17 17 0 0 1 3 4a1 1 0 0 1 1-1h3.5a1 1 0 0 1 1 1c0 1.250.2 2.45.57 3.57a1 1 0 0 1-.25 1z"/></svg>
        <span>&nbsp;610-555-0187</span>
      </li>
      <li class="contact__item">
        <svg class="contact__icon" viewBox="0 0 24 24" aria-hidden="true"><path d="M12 2a7 7 0 0 0-7 7c0 5.25 7 13 7 13s7-7.75 7-13a7 7 0 0 0-7-7zm0 9.5A2.5 2.5 0 1 1 12 6.5a2.5 2.5 0 0 1 0 5z"/></svg>
        <span>4076 Copper Ridge RD, Brenwick,<br>OH 43918</span>
      </li>
    </ul>
  </div>

  <p class="pitch">"Are you thinking about a new building on your property,<br>or renovating an existing structure? Contact".....</p>

  <svg class="card__band" viewBox="0 0 712 26" preserveAspectRatio="none" aria-hidden="true">
    <defs>
      <linearGradient id="band-back" x1="0" x2="1" y1="0" y2="0">
        <stop offset="0" stop-color="#a48f77"/>
        <stop offset="0.46" stop-color="#58381f"/>
        <stop offset="0.6" stop-color="#58381f"/>
        <stop offset="1" stop-color="#a48f77"/>
      </linearGradient>
    </defs>
    <rect width="712" height="26" fill="url(#band-back)"/>
    <polygon points="317,0 344,0 381,26 354,26" fill="#ffffff"/>
  </svg>
</section>

</body>
</html>
```